Irrigation Business needs their business cards modernised and revamped

I would like to keep my current logo, colours and revamp the format of the card.

I would like the card to be clean yet important.

Im not sure if you include texture but i would like the named logo to be indented into the card etc.

show me something alive and free something thats clinical to the point yet has a feel of achievement. i would like people to go nice card.

Target Market(s)

high end clients, corporate, sports field manger, the guys that make the decisions

Industry/Entity Type

Business

Contact Information for Business Card

nformation to be included

Dean Harlow (Director)
0487305526
dean@kolvat.biz
www.kestonfieldworks.com

instagram logo
google logo
facebook logo

Colors

Designer to choose colors to be used in the design.

Requirements
Nice to have
• indentations a really nice feel to the card good texture

```html
<!DOCTYPE html>
<html lang="en">
<head>
<meta charset="utf-8">
<title>Keston Fieldworks — Business Card</title>
<link rel="stylesheet" href="https://fonts.googleapis.com/css2?family=Montserrat:wght@700&family=Mulish:wght@400;600&display=swap">
<style>
  :root {
    --stage: #2a2a2c;
    --royal: #2f6db5;
    --royal-deep: #2a62a6;
    --navy: #3366ad;
    --sky: #38a9d8;
    --paper: #ffffff;
    --ink: #6d6f73;
    --white: #ffffff;
  }
  * { box-sizing: border-box; margin: 0; padding: 0; }
  html, body { width: 1200px; height: 900px; overflow: hidden; }
  body {
    background: var(--stage);
    display: flex; flex-direction: column; align-items: center; justify-content: center;
    gap: 36px;
    font-family: "Mulish", sans-serif;
  }
  .card {
    width: 700px; height: 400px; position: relative; overflow: hidden;
    box-shadow: 0 14px 30px rgba(0,0,0,.45);
  }
  /* Front side */
  .card--front {
    background: radial-gradient(circle at 70% 30%, #3a7cc4 0%, var(--royal) 45%, var(--royal-deep) 100%);
    display: flex; flex-direction: column; align-items: center; color: var(--white);
  }
  .front-mark {
    margin-top: 96px; width: 96px; height: 96px; border-radius: 50%;
    border: 4px solid var(--white);
  }
  .front-name {
    margin-top: 26px;
    font-family: "Montserrat", sans-serif; font-weight: 700;
    font-size: 34px; letter-spacing: .5px; text-transform: uppercase;
  }
  .front-web {
    position: absolute; bottom: 44px; left: 0; right: 0; text-align: center;
    font-size: 15px; letter-spacing: .6px;
  }
  /* Back side */
  .card--back { background: var(--paper); }
  .back-name {
    position: absolute; left: 48px; top: 40px;
    font-family: "Montserrat", sans-serif; font-weight: 700;
    font-size: 25px; color: var(--navy); text-transform: uppercase; letter-spacing: .3px;
  }
  .person { position: absolute; left: 60px; top: 132px; }
  .person-name {
    font-family: "Montserrat", sans-serif; font-weight: 700; font-size: 24px;
    color: var(--navy); text-transform: uppercase;
  }
  .person-role { font-size: 17px; color: var(--ink); margin-top: 2px; }
  .person-rule { width: 22px; height: 2px; background: var(--sky); margin-top: 16px; }
  .contacts { position: absolute; left: 56px; top: 232px; list-style: none; }
  .contacts li {
    display: flex; align-items: center; gap: 16px;
    font-size: 17px; color: var(--ink); height: 27px; letter-spacing: .4px;
  }
  .contacts svg { width: 16px; height: 16px; fill: none; stroke: var(--navy); stroke-width: 1.6; }
  .social { position: absolute; left: 58px; top: 338px; display: flex; gap: 10px; }
  .social span { width: 22px; height: 22px; border-radius: 50%; background: var(--navy); }
  .social span:nth-child(2) { background: var(--sky); }
  .emblem {
    position: absolute; right: 46px; top: 50%; transform: translateY(-50%);
    width: 300px; height: 300px; border-radius: 50%;
    border: 10px solid var(--navy); background: var(--sky);
    display: flex; align-items: center; justify-content: center; text-align: center;
  }
  .emblem-name {
    font-family: "Montserrat", sans-serif; font-weight: 700; font-size: 27px;
    line-height: 1.2; color: var(--white); text-transform: uppercase;
  }
</style>
</head>
<body>
  <section class="card card--front" aria-label="Card front">
    <div class="front-mark" aria-hidden="true"></div>
    <h1 class="front-name">Keston Fieldworks</h1>
    <p class="front-web">www.kestonfieldworks.com</p>
  </section>

  <section class="card card--back" aria-label="Card back">
    <h2 class="back-name">Keston Fieldworks</h2>
    <div class="person">
      <p class="person-name">Dean Harlow</p>
      <p class="person-role">Director</p>
      <div class="person-rule"></div>
    </div>
    <ul class="contacts">
      <li>
        <svg viewBox="0 0 16 16"><path d="M4 2l2.5 3-1.5 1.5c.8 1.8 2.2 3.2 4 4L10.5 9 13.5 11.5 12 14C7 13.5 2.5 9 2 4z"/></svg>
        0487305526
      </li>
      <li>
        <svg viewBox="0 0 16 16"><rect x="1.5" y="3.5" width="13" height="9"/><path d="M1.5 3.5L8 9l6.5-5.5"/></svg>
        dean@kolvat.biz
      </li>
      <li>
        <svg viewBox="0 0 16 16"><circle cx="8" cy="8" r="6.5"/><ellipse cx="8" cy="8" rx="3" ry="6.5"/><path d="M1.5 8h13"/></svg>
        kestonfieldworks.com
      </li>
    </ul>
    <div class="social" aria-label="Social profiles">
      <span></span><span></span><span></span>
    </div>
    <div class="emblem">
      <p class="emblem-name">Keston<br>Fieldworks</p>
    </div>
  </section>
</body>
</html>
```